Advertising company unique advertising platform

we need a logo design for a new company based in Australia Melbourne. We develop innovated advertising platform where consumer can use this platform to get regular discount, as business owner they can use this platform for free advertisement. Payment for this advertisement platform only payable every two weeks, when I generate revenue for their business

Industry/Entity Type

Advertising

Contact Information for Business Card

Dale Morven | Co-Founder |Managing Director
Suite 718 240 Wattlebrook Lane Melbourne Vic 3000

ABN 38 614 207 923
Tel: +61 0487 259 318 | Email: dale.morven@plivorantu.com

Font styles to use
Decorative
Script

Requirements
Must have
• Try few different design and some round corner business card
Should not have
• One round corner business card...try 4 different colour background not only black, make sure two side is designed. Be creative so imagine you are giving this to a client make sure has wow factor, if you can also try one design with engrave like all the logo, words look 3d feel
• The word Advertising Platform use attached file font

```html
<!DOCTYPE html>
<html lang="en">
<head>
<meta charset="utf-8">
<title>Plivorantu Business Card</title>
<link rel="stylesheet" href="https://fonts.googleapis.com/css2?family=PT+Sans:wght@400;700&display=swap">
<style>
  :root {
    --backdrop: #3a3432;
    --card: #141414;
    --card-edge: #1c1c1c;
    --silver: #9a9a9a;
    --silver-dim: #6f6f6f;
    --ink: #f2f2f2;
    --accent-red: #e8452c;
    --accent-teal: #2fd6a8;
    --accent-orange: #f47a2a;
    --divider: #8a8a8a;
  }
  * { box-sizing: border-box; margin: 0; padding: 0; }
  html, body {
    width: 1200px;
    height: 864px;
    overflow: hidden;
  }
  body {
    background: var(--backdrop);
    font-family: "PT Sans", Arial, sans-serif;
    display: flex;
    align-items: center;
    justify-content: center;
    gap: 40px;
  }
  .card {
    width: 550px;
    height: 314px;
    background: var(--card);
    border: 1px solid var(--card-edge);
    box-shadow: 0 18px 40px rgba(0,0,0,0.45);
    position: relative;
  }

  /* Front side */
  .card-front {
    display: flex;
    flex-direction: column;
    align-items: center;
    justify-content: center;
    gap: 34px;
  }
  .front-brand {
    display: flex;
    align-items: center;
    gap: 16px;
  }
  .brand-dot {
    width: 46px;
    height: 46px;
    border-radius: 50%;
    background: var(--silver-dim);
  }
  .front-brand-name {
    font-size: 42px;
    font-weight: 700;
    color: var(--silver);
    letter-spacing: 1px;
  }
  .front-website {
    font-size: 14px;
    color: var(--silver-dim);
    letter-spacing: 4px;
  }

  /* Back side */
  .card-back {
    display: flex;
    align-items: center;
    padding: 0 30px 0 34px;
  }
  .back-mark {
    width: 170px;
    display: flex;
    flex-direction: column;
    align-items: center;
    gap: 12px;
  }
  .back-mark .brand-dot {
    width: 74px;
    height: 74px;
    background: var(--accent-orange);
  }
  .back-mark-name {
    font-size: 18px;
    font-weight: 700;
    color: var(--accent-orange);
  }
  .divider {
    width: 1px;
    height: 170px;
    background: linear-gradient(to bottom, transparent, var(--divider), transparent);
    margin: 0 20px 0 10px;
  }
  .details {
    font-size: 15px;
    line-height: 1.3;
    color: var(--ink);
  }
  .person-name {
    color: var(--accent-red);
    font-weight: 700;
    font-size: 16px;
    text-transform: uppercase;
  }
  .person-role {
    color: var(--accent-teal);
    font-size: 16px;
    text-transform: uppercase;
    margin-bottom: 6px;
  }
  .contact-line {
    display: flex;
    align-items: center;
    gap: 6px;
  }
  .contact-icon {
    width: 12px;
    height: 12px;
    fill: var(--accent-red);
    flex: none;
  }
</style>
</head>
<body>
  <section class="card card-front">
    <div class="front-brand">
      <span class="brand-dot"></span>
      <span class="front-brand-name">Plivorantu</span>
    </div>
    <p class="front-website">www.plivorantu.com</p>
  </section>

  <section class="card card-back">
    <div class="back-mark">
      <span class="brand-dot"></span>
      <span class="back-mark-name">Plivorantu</span>
    </div>
    <div class="divider"></div>
    <div class="details">
      <p class="person-name">Dale Morven</p>
      <p class="person-role">Co-Founder<br>Managing Director</p>
      <p>Plivorantu</p>
      <p>ABN 38 614 207 923</p>
      <p>Suite 718 240 Wattlebrook Lane</p>
      <p>Melbourne Vic 3000</p>
      <p class="contact-line">
        <svg class="contact-icon" viewBox="0 0 24 24" aria-hidden="true"><path d="M6.6 10.8a15.1 15.1 0 0 0 6.6 6.6l2.2-2.2a1 1 0 0 1 1-.25 11.4 11.4 0 0 0 3.6.57 1 1 0 0 1 1 1V20a1 1 0 0 1-1 1A17 17 0 0 1 3 4a1 1 0 0 1 1-1h3.5a1 1 0 0 1 1 1c0 1.25.2 2.45.57 3.6a1 1 0 0 1-.25 1z"/></svg>
        +61 0487 259 318
      </p>
      <p class="contact-line">
        <svg class="contact-icon" viewBox="0 0 24 24" aria-hidden="true"><path d="M2 5h20v14H2z M2 5l10 8 10-8" fill="var(--accent-red)"/><path d="M2 5l10 8 10-8" fill="none" stroke="#141414" stroke-width="2"/></svg>
        dale.morven@plivorantu.com
      </p>
    </div>
  </section>
</body>
</html>
```